Business Cards for new orthopaedic surgery practice

My husband and I are starting our own orthopaedic surgery practice. We are looking for a business card that is uniform, but one will have my name/title and the other will have his. You can just create one design with my name on it for now. But when I choose your design as the winning design I will ask that you add another copy with his name/title.

We are looking for classy, simple, elite all in one. We like dark blues/a little gold/yellow. Something that goes with our logo. We want our logo incorporated. Here is all the info you need:
Business name: RV Bone & Vitality Center
Location: 38517 North Willowmere Ave
Maple Hollow, FL 34219
Phone: 954-218-4063
Fax: 954-582-7341
Email: info@myrvbonecare.example

Names: Lydia Vance, M.D.
Board Certified Hand and Upper Extremity Surgeon

Ebo Dansu, M.D.
Board Certified Hip & Knee Replacement/General Orthopaedic Surgeon

Can decide what you want to put on the back. Maybe a slogan:
Steady in Skill. Devoted to You

I am just going to upload our logo. The only thing is if we select you as the winning design, the location, and phone numbers may change. We will need your help to update that once fully solidified.

Industry/Entity Type

Medical

Contact Information for Business Card

Colors
0054AA
0677BA
7BADD7
CADEEF
E8F1F8
0094D4
00A9DD
6FCCEA
C7EBF8
E9F6FB

Requirements
Must have
• class, appeal,
Should not have
• We want to air on the side of masculine if we are looking at masculine vs. feminine feel. But we still want it classy, sophisticated, and something we will love

```html
<!DOCTYPE html>
<html lang="en">
<head>
<meta charset="utf-8">
<title>RV Bone &amp; Vitality Center – Business Card</title>
<link rel="stylesheet" href="https://fonts.googleapis.com/css2?family=Cinzel:wght@600;700&family=Arimo:wght@400&display=swap">
<style>
  :root {
    --navy: #1e2d5a;
    --navy-light: #283b68;
    --navy-dark: #1b2852;
    --gold: #c49a5a;
    --ink: #454545;
    --rule: #d4d4d4;
    --paper: #ffffff;
    --backdrop: #e4e4e4;
  }
  * { margin: 0; padding: 0; box-sizing: border-box; }
  html, body { width: 1200px; height: 1200px; overflow: hidden; }
  body { background: var(--backdrop); position: relative; font-family: "Arimo", Arial, sans-serif; }

  .card {
    position: absolute;
    left: 256px;
    width: 688px;
    height: 392px;
    overflow: hidden;
  }
  .card-front { top: 160px; background: var(--paper); }
  .card-back { top: 654px; background: linear-gradient(180deg, var(--navy-light), var(--navy-dark)); }

  .brand-mark {
    position: absolute;
    left: 482px; top: 50px;
    width: 162px; height: 162px;
    border: 2px solid var(--gold);
    border-radius: 50%;
    display: flex; align-items: center; justify-content: center;
    text-align: center;
    font-family: "Cinzel", Georgia, serif;
    font-weight: 700;
    font-size: 17px;
    line-height: 1.25;
    letter-spacing: 1px;
    color: var(--navy);
  }

  .doctor-name {
    position: absolute; left: 48px; top: 222px;
    font-family: "Cinzel", Georgia, serif; font-weight: 700;
    font-size: 23px; line-height: 30px; letter-spacing: 0.5px; color: var(--navy);
  }
  .doctor-title {
    position: absolute; left: 48px; top: 251px;
    font-size: 15.5px; line-height: 20px; color: var(--gold);
  }
  .divider {
    position: absolute; left: 48px; top: 279px;
    width: 596px; height: 1px; background: var(--rule);
  }

  .contact-list { position: absolute; left: 49px; top: 290px; list-style: none; }
  .contact-list li {
    display: flex; align-items: center; gap: 8px;
    height: 20.5px; font-size: 15.5px; color: var(--ink);
  }
  .contact-list svg { width: 14px; height: 14px; fill: var(--navy); flex: none; }

  .address {
    position: absolute; right: 42px; top: 290px;
    text-align: right; font-size: 15.5px; line-height: 20.5px; color: var(--ink);
    font-style: normal;
  }

  .footer-bands { position: absolute; left: 0; bottom: 0; width: 688px; height: 32px; }
  .website {
    position: absolute; right: 42px; bottom: 7px;
    font-size: 15.5px; color: #fff;
  }

  .back-mark {
    position: absolute; left: 240px; top: 84px;
    width: 208px; height: 208px;
    border: 2px solid var(--gold);
    border-radius: 50%;
    display: flex; align-items: center; justify-content: center;
    text-align: center;
    font-family: "Cinzel", Georgia, serif; font-weight: 700;
    font-size: 22px; line-height: 1.25; letter-spacing: 1.5px;
    color: #fff;
  }
  .slogan {
    position: absolute; left: 0; right: 0; top: 336px;
    text-align: center;
    font-size: 16px; letter-spacing: 3.2px;
    color: var(--gold);
  }
</style>
</head>
<body>

<section class="card card-front" aria-label="Business card front">
  <div class="brand-mark">RV Bone<br>&amp; Vitality<br>Center</div>

  <h1 class="doctor-name">LYDIA VANCE, M.D.</h1>
  <p class="doctor-title">Board Certified Hand and Upper Extremity Surgeon</p>
  <div class="divider"></div>

  <ul class="contact-list">
    <li>
      <svg viewBox="0 0 24 24" aria-hidden="true"><path d="M6.6 10.8c1.4 2.8 3.8 5.1 6.6 6.6l2.2-2.2c.3-.3.7-.4 1-.2 1.1.4 2.3.6 3.6.6.6 0 1 .4 1 1V20c0 .6-.4 1-1 1C10.6 21 3 13.4 3 4c0-.6.4-1 1-1h3.5c.6 0 1 .4 1 1 0 1.3.2 2.5.6 3.6.1.3 0 .7-.2 1L6.6 10.8z"/></svg>
      <span>954-218-4063</span>
    </li>
    <li>
      <svg viewBox="0 0 24 24" aria-hidden="true"><path d="M7 2h8l2 2v5H7V2zM3 10h18v8h-3v4H6v-4H3v-8zm5 6v4h8v-4H8z"/></svg>
      <span>954-582-7341</span>
    </li>
    <li>
      <svg viewBox="0 0 24 24" aria-hidden="true"><path d="M2 5h20v14H2V5zm2 2v.5l8 5.5 8-5.5V7H4z"/></svg>
      <span>info@myrvbonecare.example</span>
    </li>
  </ul>

  <address class="address">
    38517 North Willowmere Ave<br>
    Maple Hollow, FL 34219
  </address>

  <svg class="footer-bands" viewBox="0 0 688 32" aria-hidden="true">
    <polygon points="0,1 437,1 428,16 0,16" fill="var(--gold)"/>
    <polygon points="446,0 688,0 688,32 0,32 0,20 434,20" fill="var(--navy)"/>
  </svg>
  <p class="website">www.myrvbonecare.example</p>
</section>

<section class="card card-back" aria-label="Business card back">
  <div class="back-mark">RV Bone<br>&amp; Vitality<br>Center</div>
  <p class="slogan">STEADY IN SKILL. DEVOTED TO YOU</p>
</section>

</body>
</html>
```